Our website, is loosely based on a grant proposal submitted to the Northern Vessel Society last year for a community-based project that could improve the health of the community at large, I have attached this file for your review (underline "loosely). The idea is to create a "patient navigator" a website where patients can both learn and use as a resource for their care. I have been working on the project for some time, but my other responsibilities as a cardiologist have not allowed me time to learn and design a website of this type. Our website is intended for a spanish speaking audience and is in Spanish language. Designs in english will have to be translated. Our name: AcademiaBrisol.com: means a health university: One option is to have the website have a "university" theme. The project calls for: An initial: easy registration process: collecting name, DOB and city. Simplicity is key, many of our patients barely use computers, and this site is meant to make things easier, not complicate them. The web site should work as an extension of the doctors office, so it should be serious, creative, addictive, engaging. Doctors will see the patients in the office then refer them to the website to continue their learning about their conditions. There should be a page where patients can post questions: a panel of doctors: represented with their pictures, (in circles? around the question answered?) titles and small resumes (our "faculty") answers them. Every person that will attach themself to this website will have a title: doctors and nurses will be professors, residents and fellows will be assistant professors, aids can be PA?. The site should have a market place where people can purchase items that doctors recommend including foods, products and devices; here too, we can have a "bookshop". This should have a flexible mechanism for doctors to add their recommendations a patients can have access to them. Very important: there should be a site intended to be a classroom, this is the meat of this protect: where people can watch videos our staff will make to learn about different subjects; the site should keep track of the videos watched by the person and eventually "graduate them". These videos will be created by my staff, and added over time to the site, students should be able to "request" classes (videos). It should have a site where people can input their medications (notebook), have them stored and printed as a list if necessary. And finally it should have a contact and references section. We have set up a relationship with another site that help people count calories: and a link to this should be available. We have a link to our twitter account, This protect is intended to expand, and we hope to establish a long term relationship with the design team to expand it as needed in the future. The site is on PlanoWeb and can be seen in its current form at AcademiaBrisol.com . We have had a logo designed with specific colors of the hospital I work with and one plan is to present it to our hospital to adopt our page in it final form. Again, this site is in spanish and intended for a spanish audience.

Target Market(s)

Spanish speaking, late 30s to early 60s audience.

Industry/Entity Type

Community

Number of Pages Required

4 page

Font styles to use
Sans Serif

Colors
a64599
fceff5
3277b5

Requirements
Must have
• A simple, accesible look
Nice to have
• Animations, moving parts
Should not have
• English

```html
<!DOCTYPE html>
<html lang="es">
<head>
<meta charset="utf-8">
<title>AcademiaBrisol · Tu salud comienza hoy</title>
<link href="https://fonts.googleapis.com/css2?family=Roboto:wght@300;400;500;700&display=swap" rel="stylesheet">
<style>
:root{
  --purple:#a64599;
  --purple-soft:#c78bbf;
  --pink:#fceff5;
  --blue:#3277b5;
  --blue-dark:#244f7d;
  --grey-bg:#f5f5f5;
  --text:#444;
  --muted:#888;
  --white:#fff;
}
*{box-sizing:border-box;margin:0;padding:0}
html,body{width:1200px;height:2278px;overflow:hidden}
body{font-family:'Roboto',Arial,sans-serif;color:var(--text);background:var(--white);position:relative}
.wrap{position:relative;width:858px;margin-left:173px;height:100%}
.img-fill{position:absolute}
.btn{display:inline-block;background:var(--purple);color:var(--white);font-size:13px;font-weight:500;text-align:center;line-height:36px;height:36px;width:122px}
.btn-dark{position:absolute;right:0;top:22px;width:276px;height:50px;line-height:50px;background:var(--blue-dark);color:var(--white);font-size:17px;font-weight:500;text-align:center;text-transform:uppercase}
.brand{font-weight:300;color:var(--purple);letter-spacing:-0.5px}

/* header */
.site-header{height:110px;background:var(--pink)}
.site-header .brand{position:absolute;left:0;top:30px;font-size:42px}
.call{position:absolute;right:0;top:32px;text-align:right}
.call small{display:block;font-size:12px;color:var(--muted)}
.call strong{display:block;font-size:19px;font-weight:400;color:var(--purple);margin-top:3px}
.call svg{position:absolute;left:-34px;top:22px}

/* nav */
.main-nav{height:60px;background:var(--blue)}
.main-nav ul{list-style:none;display:flex;height:60px}
.main-nav li{height:60px;line-height:60px;text-align:center;color:var(--white);font-size:13px;border-right:1px solid rgba(255,255,255,.25)}
.main-nav li:first-child{border-left:1px solid rgba(255,255,255,.25)}
.main-nav li.active{background:var(--purple)}
.nav-social{display:flex;gap:18px;justify-content:center;align-items:center}
.nav-social span{width:14px;height:14px;border-radius:50%;background:var(--white);display:block}

/* hero */
.hero{position:relative;height:343px;overflow:hidden}
.hero-photo{left:0;top:0;width:1200px;height:343px;background:linear-gradient(90deg,#c9b39d 0%,#e6d8c8 30%,#eeeeee 55%,#f7f7f7 100%)}
.hero-arrow{position:absolute;top:143px;width:56px;height:56px;border:2px solid var(--blue);border-radius:50%;display:flex;align-items:center;justify-content:center;background:rgba(255,255,255,.35)}
.hero-arrow.prev{left:46px}.hero-arrow.next{right:46px}
.hero-copy{position:absolute;right:128px;top:72px;text-align:right}
.hero-copy .brand{font-size:46px}
.hero-copy p{font-size:24px;color:var(--purple);margin-top:8px}
.dots{display:flex;gap:6px;justify-content:flex-end;margin-top:14px;padding-right:4px}
.dots i{width:11px;height:11px;border:1.5px solid var(--blue);border-radius:50%;display:block}
.quote-title{position:absolute;left:173px;top:223px;width:406px;height:50px;background:rgba(255,255,255,.88);color:var(--purple);font-size:25px;line-height:50px;padding-left:34px}
.quote-form{position:absolute;left:173px;top:273px;width:858px;height:70px;background:var(--purple);display:flex;gap:8px;padding:20px 22px}
.quote-form span{flex:1;height:30px;background:var(--purple-soft);color:var(--white);font-size:10px;line-height:30px;padding-left:12px}
.quote-form .submit{background:var(--white);color:var(--purple);text-align:center;padding:0;font-weight:500}

/* bands */
.band{height:99px;background:var(--blue);position:relative}
.band p{position:absolute;left:0;top:37px;color:var(--white);font-size:19px;text-transform:uppercase}
.band .btn-dark{top:24px}

/* welcome */
.welcome{height:252px;position:relative}
.welcome h1{position:absolute;left:0;top:52px;font-size:28px;font-weight:400;color:var(--blue)}
.welcome h1 .brand{font-size:30px}
.welcome p{position:absolute;left:0;top:96px;width:420px;font-size:10.5px;line-height:13px;color:var(--text)}
.welcome .btn{position:absolute;left:0;top:156px}
.video-box{left:479px;top:32px;width:379px;height:186px;border:1px solid #ddd;background:linear-gradient(90deg,#e9d9bb,#cfd7c9 50%,#b8b4ad)}
.play{position:absolute;left:50%;top:50%;width:52px;height:52px;margin:-26px 0 0 -26px;border-radius:50%;background:rgba(70,70,70,.75);display:flex;align-items:center;justify-content:center}

/* services */
.services{height:333px;background:var(--grey-bg);position:relative}
.doctor-photo{left:165px;top:-52px;width:360px;height:385px;background:linear-gradient(180deg,#f0e3cf 0%,#f4f4f4 35%,#e8ecee 100%);border-radius:160px 160px 0 0}
.services h2{position:absolute;left:455px;top:42px;font-size:38px;font-weight:400;color:var(--purple)}
.services ul{position:absolute;left:455px;top:108px;list-style:none}
.services li{font-size:15px;color:var(--text);margin-bottom:13px;padding-left:26px;position:relative;text-transform:uppercase}
.services li svg{position:absolute;left:0;top:2px}
.services p{position:absolute;left:455px;top:178px;width:403px;font-size:10.5px;line-height:13px}
.services .btn{position:absolute;left:455px;top:240px}

/* classes */
.classes{height:295px;position:relative}
.class-photo{left:0;top:31px;width:240px;height:232px;border:1px solid #ddd;background:linear-gradient(90deg,#efefef,#d8dbe0 50%,#e4d6c4)}
.class-body{position:absolute;left:274px;top:38px;width:290px}
.class-body h3{font-size:23px;font-weight:400;color:var(--blue);text-transform:uppercase}
.class-body p{font-size:10.5px;line-height:13px;margin-top:8px}
.video-link{position:absolute;left:274px;top:181px;display:flex;align-items:center;gap:14px;font-size:15px}
.video-thumb{position:relative;width:116px;height:69px;background:linear-gradient(90deg,#c89a7c,#e9dccf)}
.video-thumb .play{width:30px;height:30px;margin:-15px 0 0 -15px}
.links{position:absolute;left:599px;top:31px;width:259px}
.links h4{height:56px;background:var(--pink);color:var(--purple);font-size:19px;font-weight:400;line-height:56px;padding-left:20px}
.links li{list-style:none;height:43px;line-height:43px;border-bottom:1px solid #d9d9d9;font-size:11px;color:var(--blue-dark);padding-left:20px;position:relative;text-transform:uppercase}
.links li svg{position:absolute;right:16px;top:15px}

/* features */
.features{height:284px;background:var(--pink);position:relative}
.feature{position:absolute;width:400px;display:flex;gap:18px}
.feature .thumb{width:96px;height:96px;border-radius:50%;border:3px solid var(--purple);flex:none;position:relative;overflow:hidden}
.feature .thumb i{position:absolute;inset:4px;border-radius:50%;display:block}
.feature h5{font-size:11px;color:var(--purple);font-weight:700;margin-top:22px;text-transform:uppercase}
.feature p{font-size:10.5px;line-height:13px;margin-top:6px;color:var(--text)}

/* shops */
.shops{height:234px;position:relative}
.shop{position:absolute;top:32px;width:423px;height:172px;border:1px solid #ddd}
.shop .fill{inset:0}
.shop span{position:absolute;left:0;right:0;bottom:0;height:52px;background:rgba(255,255,255,.6);color:var(--blue);text-align:center;font-size:26px;font-weight:500;line-height:52px}

/* footer */
.site-footer{height:120px;background:var(--pink);position:relative}
.site-footer .brand{position:absolute;left:0;top:36px;font-size:40px}
.foot-social{position:absolute;right:0;top:48px;display:flex;gap:10px}
.foot-social span{width:26px;height:26px;border-radius:50%;background:#b5b5b5;display:block}
.copyright{height:50px;text-align:center;font-size:12px;color:var(--muted);line-height:30px}
</style>
</head>
<body>

<header class="site-header">
  <div class="wrap">
    <div class="brand">AcademiaBrisol</div>
    <div class="call">
      <svg width="22" height="22" viewBox="0 0 24 24"><path fill="#a64599" d="M6.6 10.8a15.1 15.1 0 0 0 6.6 6.6l2.2-2.2a1 1 0 0 1 1-.25 11.4 11.4 0 0 0 3.6.57 1 1 0 0 1 1 1V20a1 1 0 0 1-1 1A17 17 0 0 1 3 4a1 1 0 0 1 1-1h3.5a1 1 0 0 1 1 1c0 1.25.2 2.45.57 3.57a1 1 0 0 1-.25 1z"/></svg>
      <small>Llámenos hoy mismo!</small>
      <strong>0800 (555) 0142</strong>
    </div>
  </div>
</header>

<nav class="main-nav">
  <div class="wrap">
    <ul>
      <li class="active" style="width:104px">INICIO</li>
      <li style="width:118px">ACERCA</li>
      <li style="width:116px">TIENDA</li>
      <li style="width:99px">BLOG</li>
      <li style="width:93px">FAQ</li>
      <li style="width:135px">CONTACTO</li>
      <li class="nav-social" style="width:193px"><span></span><span></span><span></span><span></span></li>
    </ul>
  </div>
</nav>

<section class="hero">
  <div class="img-fill hero-photo" role="img" aria-label="Fotografía de una pareja sonriente en casa con una tableta"></div>
  <div class="hero-arrow prev"><svg width="16" height="22" viewBox="0 0 16 22"><path d="M12 2 3 11l9 9" fill="none" stroke="#3277b5" stroke-width="2"/></svg></div>
  <div class="hero-arrow next"><svg width="16" height="22" viewBox="0 0 16 22"><path d="m4 2 9 9-9 9" fill="none" stroke="#3277b5" stroke-width="2"/></svg></div>
  <div class="hero-copy">
    <div class="brand">AcademiaBrisol</div>
    <p>TU SALUD COMIENZA HOY!</p>
    <div class="dots"><i></i><i></i><i></i></div>
  </div>
  <div class="quote-title">Obtenga ahora un Presupuesto!</div>
  <div class="quote-form">
    <span>NOMBRE</span><span>EMAIL</span><span>Fecha de nacimiento</span><span class="submit">CONTACTO EE.UU. AHORA!</span>
  </div>
</section>

<section class="band">
  <div class="wrap">
    <p>Contacto EE.UU. ahora y obtenga la salud mejor!</p>
    <div class="btn-dark">Cita ahora</div>
  </div>
</section>

<section class="welcome">
  <div class="wrap">
    <h1>Bienvenidos al <span class="brand">AcademiaBrisol</span></h1>
    <p>Aquí aprenderá sobre su salud paso a paso, con la guía de nuestros médicos y enfermeras. Cada lección es breve, clara y pensada para usted y su familia. Vea los videos, haga preguntas y lleve un registro de sus medicamentos en un solo lugar, desde su casa, a su ritmo.</p>
    <a class="btn">leer más</a>
    <div class="img-fill video-box" role="img" aria-label="Video de una enfermera conversando con una paciente mayor">
      <div class="play"><svg width="18" height="20" viewBox="0 0 18 20"><path d="M2 1v18l15-9z" fill="#fff"/></svg></div>
    </div>
  </div>
</section>

<section class="services">
  <div class="wrap">
    <div class="img-fill doctor-photo" role="img" aria-label="Fotografía de una doctora sonriente con estetoscopio"></div>
    <h2>NUESTROS SERVICIOS</h2>
    <ul>
      <li><svg width="16" height="14" viewBox="0 0 16 14"><path d="m1 1 6 6-6 6M8 1l6 6-6 6" fill="none" stroke="#a64599" stroke-width="2"/></svg>Paciente aprender para el cuidado</li>
      <li><svg width="16" height="14" viewBox="0 0 16 14"><path d="m1 1 6 6-6 6M8 1l6 6-6 6" fill="none" stroke="#a64599" stroke-width="2"/></svg>Uso recursos del paciente</li>
    </ul>
    <p>Ofrecemos clases en video, un cuaderno de medicamentos, preguntas a nuestro cuerpo de profesores y una tienda con productos recomendados por sus médicos para su cuidado diario...</p>
    <a class="btn">leer más</a>
  </div>
</section>

<section class="classes">
  <div class="wrap">
    <div class="img-fill class-photo" role="img" aria-label="Fotografía de un médico explicando un documento a una paciente"></div>
    <div class="class-body">
      <h3>Clases de estudiantes</h3>
      <p>Nuestras clases en video explican cada tema con palabras sencillas. Usted puede ver las lecciones cuando quiera, repetirlas y solicitar nuevos temas. Al completar el programa, recibirá su graduación de paciente informado.</p>
    </div>
    <div class="video-link">
      <div class="video-thumb" role="img" aria-label="Miniatura de video de una clase">
        <div class="play"><svg width="10" height="12" viewBox="0 0 18 20"><path d="M2 1v18l15-9z" fill="#fff"/></svg></div>
      </div>
      Vea los videos!
    </div>
    <div class="links">
      <h4>ENLACES DE INTERÉS</h4>
      <ul>
        <li>Solicitud de clases<svg width="8" height="12" viewBox="0 0 8 12"><path d="m1 1 5 5-5 5" fill="none" stroke="#a64599" stroke-width="2"/></svg></li>
        <li>Navegación del paciente<svg width="8" height="12" viewBox="0 0 8 12"><path d="m1 1 5 5-5 5" fill="none" stroke="#a64599" stroke-width="2"/></svg></li>
        <li>Librería<svg width="8" height="12" viewBox="0 0 8 12"><path d="m1 1 5 5-5 5" fill="none" stroke="#a64599" stroke-width="2"/></svg></li>
        <li>FAQ<svg width="8" height="12" viewBox="0 0 8 12"><path d="m1 1 5 5-5 5" fill="none" stroke="#a64599" stroke-width="2"/></svg></li>
      </ul>
    </div>
  </div>
</section>

<section class="band">
  <div class="wrap">
    <p>Para aprender, para solicitar las clases de video!</p>
    <div class="btn-dark">Solicitud de clases</div>
  </div>
</section>

<section class="features">
  <div class="wrap">
    <div class="feature" style="left:0;top:32px">
      <div class="thumb"><i role="img" aria-label="Foto de una paciente leyendo" style="background:linear-gradient(135deg,#d9b79a,#f2e6da)"></i></div>
      <div><h5>Aprenda sobre su salud</h5><p>Lecciones cortas y claras para entender su condición y cuidarse mejor cada día.</p></div>
    </div>
    <div class="feature" style="left:458px;top:32px">
      <div class="thumb"><i role="img" aria-label="Foto de un hombre usando una tableta" style="background:linear-gradient(135deg,#7fa6c8,#dfe8f0)"></i></div>
      <div><h5>Pregunte a los profesores</h5><p>Envíe sus dudas y nuestro panel de médicos le responderá con atención y cuidado.</p></div>
    </div>
    <div class="feature" style="left:0;top:152px">
      <div class="thumb"><i role="img" aria-label="Foto de una mujer con una computadora" style="background:linear-gradient(135deg,#b7683e,#e8d2c0)"></i></div>
      <div><h5>Cuaderno de medicamentos</h5><p>Guarde su lista de medicinas e imprímala cuando la necesite para su próxima cita.</p></div>
    </div>
    <div class="feature" style="left:458px;top:152px">
      <div class="thumb"><i role="img" aria-label="Foto de un hombre sonriente" style="background:linear-gradient(135deg,#5f94c2,#e4eef5)"></i></div>
      <div><h5>Cuente sus calorías</h5><p>Acceda a nuestro sitio asociado para llevar el control de su alimentación diaria.</p></div>
    </div>
  </div>
</section>

<section class="shops">
  <div class="wrap">
    <div class="shop" style="left:0">
      <div class="img-fill fill" role="img" aria-label="Fotografía del interior de una librería" style="background:linear-gradient(180deg,#d9d6d3,#a8a29c 60%,#cfcac5)"></div>
      <span>LIBRERÍA</span>
    </div>
    <div class="shop" style="left:435px">
      <div class="img-fill fill" role="img" aria-label="Fotografía de estantes de un mercado con alimentos" style="background:linear-gradient(90deg,#d8c45a,#e8783c 45%,#9fb7d1 70%,#e6d2b5)"></div>
      <span>MARKETSHOP</span>
    </div>
  </div>
</section>

<footer class="site-footer">
  <div class="wrap">
    <div class="brand">AcademiaBrisol</div>
    <div class="foot-social"><span></span><span></span><span></span><span></span></div>
  </div>
</footer>
<div class="copyright">Derechos de autor © 2014 Academiabrisol</div>

</body>
</html>
```